Harborview Estates Business Card for Apartment Buildings

Create business cards for resident managers who run apartment buildings. The audience is the public who are searching for apartment rentals, and current residents who live at the apartment building. Key design element will be incorporating the company logo, however, the logo cannot dominate. The building name and manager name are more important than the logo. Current business card design leaves little room for copy, so we may need to reduce the size on the current card to allow for more space for copy.

Target Market(s)

Adults 18-65 years of age, who are looking for an apartment rental, plus current residents who live at our apartment buildings.

Industry/Entity Type

Property Management

Contact Information for Business Card

A major design element will be use of the company logo. Important property and manager contact information must be part of the design. The size of the logo will need to be reduced to make room for building and manager contact copy.

Font styles to use
Sans Serif

Colors
3176b5
000000
959595
ffffff

Requirements
Must have
• 1) Incorporate the company logo.
• 2) Use the company colors (dark blue, black/grey, over white).
• 3) FEATURE THE BUILDING NAME
• 4) FEATURE THE MANAGER NAME
• 5) The company name is less important than BUILDING and MANAGER
• 6) Manager contact information
• **SEE ATTACHED CREATIVE BRIEF**
Nice to have
• 1) Back of card logo watermark
• 2) Ability to write notes on back of carfd
Should not have
• Avoid letting the company logo dominate the card, the building name and manager are more important than the company logo.

```html
<!DOCTYPE html>
<html lang="en">
<head>
<meta charset="utf-8">
<title>Harborview Estates – Resident Manager Card</title>
<link href="https://fonts.googleapis.com/css2?family=Work+Sans:wght@400;500;600&display=swap" rel="stylesheet">
<style>
  :root {
    --brand-blue: #3176b5;
    --brand-blue-deep: #1f5f8e;
    --ink: #000000;
    --grey: #959595;
    --paper: #ffffff;
    --card-face: #eef1f3;
    --backdrop: #d9d6d2;
  }
  * { margin: 0; padding: 0; box-sizing: border-box; }
  html, body {
    width: 1200px;
    height: 1047px;
    overflow: hidden;
    background: var(--backdrop);
    font-family: "Work Sans", Arial, sans-serif;
  }
  .card {
    position: absolute;
    left: 150px;
    top: 290px;
    width: 946px;
    height: 514px;
    border-radius: 20px;
    background: var(--card-face);
    overflow: hidden;
    box-shadow: 0 12px 30px rgba(0,0,0,0.18);
  }
  .card__panel {
    position: absolute;
    inset: 0;
    background: linear-gradient(160deg, var(--brand-blue) 0%, var(--brand-blue-deep) 100%);
    clip-path: polygon(0 0, 665px 0, 610px 100%, 0 100%);
  }
  .card__mark-area {
    position: absolute;
    left: 520px;
    top: 10px;
    width: 500px;
    height: 500px;
    border-radius: 50%;
    background: radial-gradient(circle at 55% 50%, rgba(149,149,149,0.35), rgba(149,149,149,0.12) 70%, rgba(149,149,149,0) 72%);
  }
  .card__content {
    position: absolute;
    left: 32px;
    top: 50px;
    color: var(--paper);
  }
  .brand {
    display: flex;
    align-items: center;
    gap: 12px;
    margin-bottom: 44px;
  }
  .brand__dot {
    width: 18px;
    height: 18px;
    border-radius: 50%;
    background: var(--paper);
  }
  .brand__name {
    font-size: 24px;
    font-weight: 600;
    letter-spacing: 1px;
    text-transform: uppercase;
    color: var(--paper);
  }
  .manager__name {
    font-size: 30px;
    font-weight: 600;
    letter-spacing: 0.6px;
    text-transform: uppercase;
  }
  .manager__title {
    font-size: 21px;
    font-weight: 400;
    margin-top: 4px;
    letter-spacing: 0.4px;
  }
  .property {
    margin-top: 18px;
    font-size: 21px;
    line-height: 28px;
    letter-spacing: 0.5px;
  }
  .property__building {
    font-size: 24px;
    font-weight: 600;
    line-height: 32px;
  }
  .contact {
    margin-top: 20px;
    list-style: none;
    font-size: 21px;
    line-height: 28px;
    letter-spacing: 0.5px;
  }
  .contact li {
    display: flex;
    align-items: center;
    gap: 14px;
  }
  .contact svg {
    width: 13px;
    height: 13px;
    fill: none;
    stroke: var(--paper);
    stroke-width: 1.8;
  }
</style>
</head>
<body>
  <div class="card">
    <div class="card__mark-area" role="img" aria-label="Large company emblem watermark area"></div>
    <div class="card__panel"></div>
    <div class="card__content">
      <div class="brand">
        <span class="brand__dot"></span>
        <span class="brand__name">Harborview Estates</span>
      </div>
      <div class="manager">
        <div class="manager__name">Marisol Delgado</div>
        <div class="manager__title">Resident Manager</div>
      </div>
      <div class="property">
        <div class="property__building">Cedar Court Apartments</div>
        <div>2480 Larkspur Avenue</div>
        <div>Port Alder, CA 91555</div>
      </div>
      <ul class="contact">
        <li><svg viewBox="0 0 14 14"><path d="M3 1.5l2.5 2.5-1.5 1.5c1 2 2.5 3.5 4.5 4.5l1.5-1.5 2.5 2.5-2 2C6 12.5 1.5 8 1 3.5z"/></svg>555-240-1180</li>
        <li><svg viewBox="0 0 14 14"><rect x="3.5" y="1" width="7" height="12" rx="1.2"/><path d="M6 11h2"/></svg>555-318-4472</li>
        <li><svg viewBox="0 0 14 14"><rect x="1.5" y="5" width="11" height="6" rx="1"/><path d="M4 5V1.5h6V5M4 11v1.5h6V11"/></svg>555-406-2290</li>
        <li><svg viewBox="0 0 14 14"><rect x="1.5" y="3" width="11" height="8" rx="1"/><path d="M1.5 3.5L7 8l5.5-4.5"/></svg>marisol@harborviewest.com</li>
        <li><svg viewBox="0 0 14 14"><circle cx="7" cy="7" r="5.5"/><path d="M1.5 7h11M7 1.5c-2.5 3-2.5 8 0 11M7 1.5c2.5 3 2.5 8 0 11"/></svg>www.harborviewest.com</li>
      </ul>
    </div>
  </div>
</body>
</html>
```